Venture 482 - Lumora Book Cover

I am looking for a Lumora book cover for my book about "Venture 482".
The Book is Titled:
Venture 482 Ascended
Shaping Outcomes: Paths To Unlocking Cosmic Truths
Author is Dorian Pell
Here is a book description that may help you understand more about it:
Inspired by the genius of Edwin Marlowe, this comprehensive guide delves into the ancient wisdom and cutting-edge science behind the 482 method, a powerful tool for manifesting your desires. Whether you're seeking personal growth, financial success, or spiritual enlightenment, this book provides advanced techniques and methods to transform your dreams into reality.
Any questions please ask.
Thanks
Owen

```html
<!DOCTYPE html>
<html lang="en">
<head>
<meta charset="utf-8">
<title>Venture 482 Ascended — Dorian Pell</title>
<link rel="stylesheet" href="https://fonts.googleapis.com/css2?family=Cinzel:wght@400;700;900&family=Montserrat:wght@300&family=Tinos&display=swap">
<style>
  :root {
    --page-bg: #e4e4e2;
    --sky-top: #14294a;
    --sky-mid: #3f74aa;
    --sky-low: #8fb3d6;
    --horizon: #d9dde3;
    --plain: #9c8f72;
    --terrace: #d2c5ae;
    --terrace-dark: #2b2621;
    --cream: #fbeee0;
    --author: #f1d6c8;
    --title-shadow: rgba(20, 30, 50, 0.55);
    --edition: #fbf4d8;
  }
  * { margin: 0; padding: 0; box-sizing: border-box; }
  html, body {
    width: 1200px; height: 1131px; overflow: hidden;
    background: var(--page-bg);
  }
  .cover {
    position: absolute; left: 240px; top: 25px;
    width: 720px; height: 1080px;
    border-radius: 10px; overflow: hidden;
  }
  .cover-art {
    position: absolute; inset: 0;
    background: linear-gradient(180deg,
      var(--sky-top) 0%, var(--sky-mid) 28%, var(--sky-low) 50%,
      var(--horizon) 63%, var(--plain) 66%, var(--plain) 72%,
      var(--terrace) 74%, var(--terrace) 82%, var(--terrace-dark) 100%);
  }
  .cover-text {
    position: absolute; inset: 0;
    text-align: center; color: var(--cream);
  }
  .author {
    position: absolute; top: 66px; left: 0; right: 0;
    font-family: "Cinzel", serif; font-weight: 400;
    font-size: 44px; letter-spacing: 0.3em; padding-left: 0.3em;
    color: var(--author);
  }
  .title-word {
    position: absolute; top: 158px; left: 0; right: 0;
    font-family: "Cinzel", serif; font-weight: 900;
    font-size: 92px; letter-spacing: -0.01em; line-height: 1;
    text-shadow: 4px 6px 10px var(--title-shadow);
  }
  .title-number {
    position: absolute; top: 236px; left: 0; right: 0;
    font-family: "Cinzel", serif; font-weight: 700;
    font-size: 250px; line-height: 1; letter-spacing: -0.04em;
    text-shadow: 6px 10px 14px var(--title-shadow);
  }
  .edition {
    position: absolute; top: 478px; left: 0; right: 0;
    font-family: "Cinzel", serif; font-weight: 700;
    font-size: 50px; letter-spacing: 0.42em; padding-left: 0.42em;
    color: var(--edition);
    text-shadow: 3px 3px 0 #1a1a1a;
  }
  .subtitle {
    position: absolute; top: 926px; left: 0; right: 0;
    font-family: "Montserrat", sans-serif; font-weight: 300;
    font-size: 28px; letter-spacing: 0.01em;
  }
  .tagline {
    position: absolute; top: 972px; left: 0; right: 0;
    font-family: "Tinos", serif; font-size: 25px; line-height: 1.3;
  }
</style>
</head>
<body>
  <main class="cover">
    <div class="cover-art" role="img" aria-label="Photograph of a young man standing barefoot on a stone terrace, seen from behind, looking over wide rolling plains under a bright blue sky with clouds"></div>
    <div class="cover-text">
      <p class="author">DORIAN PELL</p>
      <h1>
        <span class="title-word">VENTURE</span>
        <span class="title-number">482</span>
        <span class="edition">ASCENDED</span>
      </h1>
      <p class="subtitle">SHAPING OUTCOMES:</p>
      <p class="tagline">Paths to unlocking<br>cosmic truths</p>
    </div>
  </main>
</body>
</html>
```